Wellbrook Talking Therapies Hub Swindon

We need a design for magazine advert, ideally high resolution to advertise our counselling centre. we would like this to include a photo of two people talking, as if in a counselling session. See our logo and colour range on our website. www.wbtth-swindon.co.uk
The photo should not include cups of coffee, clipboards, desks, people touching. it needs to be two people in armchairs sympathetically listening and looking at each other.
The font type is Great Vibes on the logo. Our design should communicate a centre of excellence delivering high quality, professional services in stylishly furnished surroundings.

Hello Everyone We have had a number of designs that look quite promising but are missing the brief. Can I reiterate that we need a photograph of 2 people seated talking to each other in a sincere way. There shouldn't be office chairs but comfortable chairs. There should be no physical contact. There should be no clipboards.Thank you very muchHeather Added Sunday, March 12, 2017

Target Market(s)

people seeking counselling and psychotherapy

Font styles to use
Other font styles liked:
• Great Vibes as in our logo for some of the print. See attached file.

Requirements
Must have
• good photograph
• Two high res Pixavend photos:
• https://pixavend-files.example-cdn.net/download?id=a81kd93jf02mdl47xq
• https://pixavend-files.example-cdn.net/download?id=z57pw20ne84bvc13ty
Nice to have
• Watermark in keeping with our logo.
Should not have
• Darkness

```html
<!DOCTYPE html>
<html lang="en">
<head>
<meta charset="utf-8">
<title>Wellbrook Talking Therapies Hub – Magazine Advert</title>
<link rel="stylesheet" href="https://fonts.googleapis.com/css2?family=Great+Vibes&family=Montserrat:wght@400;500;600&display=swap">
<style>
  :root {
    --page-bg: #e9e9e9;
    --cream: #f3ecdd;
    --brown: #3a2f2d;
    --sage: #a9bb8c;
    --sage-light: #c9d5b2;
    --olive-text: #7b8a2c;
    --phone-green: #93b47e;
    --ink: #2b2322;
    --white: #ffffff;
  }
  * { box-sizing: border-box; margin: 0; padding: 0; }
  html, body {
    width: 1200px; height: 1200px; overflow: hidden;
    background: var(--page-bg);
    font-family: "Montserrat", Arial, sans-serif;
  }
  .advert {
    position: absolute; left: 190px; top: 20px;
    width: 820px; height: 1160px;
    background: var(--cream);
    box-shadow: 0 14px 40px rgba(0,0,0,0.18);
    overflow: hidden;
  }
  .advert-shapes { position: absolute; inset: 0; width: 100%; height: 100%; }
  .headline {
    position: absolute; left: 0; width: 820px; text-align: center;
    font-family: "Great Vibes", cursive; font-weight: 400;
    color: var(--ink); font-size: 50px; line-height: 1;
  }
  .headline-line-1 { top: 515px; left: 14px; }
  .headline-line-2 { top: 577px; left: -18px; }
  .intro {
    position: absolute; left: 171px; top: 648px; width: 340px;
    font-size: 16.5px; line-height: 24.5px; color: var(--ink);
  }
  .intro strong { color: var(--olive-text); font-weight: 600; }
  .contact {
    position: absolute; left: 66px; top: 964px; width: 320px;
    color: var(--white);
  }
  .contact-hours { font-size: 14.5px; line-height: 18px; }
  .contact-phone {
    font-size: 32px; line-height: 36px; color: var(--phone-green);
    font-weight: 400; letter-spacing: 0.5px; margin-top: 2px;
  }
  .contact-address { font-size: 14.5px; line-height: 18px; margin-top: 18px; }
  .contact-web { font-size: 14.5px; font-weight: 600; margin-top: 18px; }
  .brand {
    position: absolute; left: 430px; top: 1035px; width: 300px; text-align: center;
  }
  .brand-dot {
    display: block; width: 46px; height: 46px; border-radius: 50%;
    background: var(--sage); margin: 0 auto 14px;
  }
  .brand-name {
    font-family: "Montserrat", Arial, sans-serif; font-weight: 500;
    font-size: 19px; line-height: 24px; color: var(--brown);
  }
</style>
</head>
<body>
<main class="advert">
  <svg class="advert-shapes" viewBox="0 0 777 1100" preserveAspectRatio="none" aria-hidden="false">
    <defs>
      <linearGradient id="sessionPhotoTone" x1="0" y1="0" x2="1" y2="1">
        <stop offset="0" stop-color="#6f7a63"/>
        <stop offset="0.45" stop-color="#b9bcae"/>
        <stop offset="1" stop-color="#d8d3c8"/>
      </linearGradient>
      <linearGradient id="teamPhotoTone" x1="0" y1="0" x2="1" y2="0">
        <stop offset="0" stop-color="#e6e2df"/>
        <stop offset="0.6" stop-color="#d9c6bd"/>
        <stop offset="1" stop-color="#cfd9d4"/>
      </linearGradient>
    </defs>
    <path class="accent-band" d="M0,0 H777 V255 C700,360 620,430 520,462 C400,470 200,470 0,560 Z" fill="var(--sage-light)"/>
    <path class="session-photo" role="img" aria-label="Photo: a therapist and a client seated in comfortable chairs talking in a bright room"
      d="M0,0 H777 V240 C700,345 620,415 520,448 C400,460 200,460 0,545 Z" fill="url(#sessionPhotoTone)"/>
    <path class="team-photo" role="img" aria-label="Photo: two smiling therapists from the centre's team"
      d="M420,840 C520,720 650,640 777,612 V702 C650,745 520,800 420,840 Z" fill="url(#teamPhotoTone)"/>
    <path class="contact-panel" d="M0,935 C100,845 300,822 420,838 C370,860 345,960 318,1100 H0 Z" fill="var(--brown)"/>
    <path class="brand-panel" d="M318,1100 C345,960 370,860 420,838 C520,800 650,745 777,702 V1100 Z" fill="var(--white)"/>
  </svg>

  <h1 class="headline headline-line-1">Confidential Therapeutic Services</h1>
  <p class="headline headline-line-2">in the Heart of Old Town</p>

  <p class="intro">We have over <strong>30 carefully selected, qualified and professional therapists</strong> offering a range of services to help individuals, families and couples.</p>

  <section class="contact">
    <p class="contact-hours">Appointments available<br>throughout the day and evening</p>
    <p class="contact-phone">01632 960418</p>
    <p class="contact-address">14 Kingsmead Lane, Old Town,<br>Swindon SN1 9ZZ</p>
    <p class="contact-web">www.wbtth-swindon.co.uk</p>
  </section>

  <div class="brand">
    <span class="brand-dot"></span>
    <p class="brand-name">Wellbrook Talking Therapies Hub</p>
  </div>
</main>
</body>
</html>
```